Real estate broker business card

Want a modern celan but effective business card for my residential and commercial real estate business. I want the back of the card to advertise my services and to capture business. I have attached the back of my current business card fore ideas
Updates

Logos, photo and text updates added! Added Saturday, September 3, 2016

Project Deadline Extended Reason: LOGOS, PHOTOS AND TEST JUST UPLOADED! I'M READY TO PICK A DESIGN! THANK YOU! Added Saturday, September 3, 2016

Target Market(s)

home buyers and seller. commercial buyers and sellers

Industry/Entity Type

Real Estate

Contact Information for Business Card

must have my contact information and my photo

Requirements
Must have
• Carla Ventrino
• Owner & Qualifying Broker
• Ventrino Real Estate Services
• 505.718.2094
• carla@ventrinohomes.example
• www.ventrinohomes.example
Nice to have
• metallic
• Business capture text: " Don't buy or lease property without someone looking out for your best interests. I will represent you on your home or investment purchase for FREE!"
• "Home owners, call today to receive a FREE market analysis for your homes value!

```html
<!DOCTYPE html>
<html lang="en">
<head>
<meta charset="utf-8">
<title>Ventrino Real Estate Services – Business Card</title>
<link rel="stylesheet" href="https://fonts.googleapis.com/css2?family=Source+Sans+3:wght@400;600&display=swap">
<style>
  :root {
    --bg: #e9e6e1;
    --card-black: #050505;
    --teal: #1a8c9c;
    --teal-light: #1fa0b0;
    --silver-light: #e4e6e8;
    --silver-dark: #8e9397;
    --white: #ffffff;
    --photo-mid: #5a3f33;
    --photo-light: #d9cbc4;
  }
  * { box-sizing: border-box; margin: 0; padding: 0; }
  html, body { width: 1200px; height: 900px; overflow: hidden; }
  body {
    background: var(--bg);
    font-family: "Source Sans 3", sans-serif;
    position: relative;
  }
  .card {
    position: absolute;
    left: 290px;
    width: 620px;
    height: 355px;
    background: var(--card-black);
    box-shadow: 0 8px 24px rgba(0,0,0,0.25);
    overflow: hidden;
    color: var(--white);
  }
  .card--back { top: 70px; }
  .card--front { top: 475px; }

  /* Back */
  .brand {
    position: absolute;
    top: 58px;
    left: 0;
    right: 0;
    display: flex;
    justify-content: center;
    align-items: center;
    gap: 14px;
  }
  .brand__mark {
    width: 44px; height: 44px;
    border-radius: 50%;
    background: var(--teal);
  }
  .brand__name {
    color: var(--teal);
    font-weight: 600;
    font-size: 30px;
    letter-spacing: 1px;
  }
  .pitch {
    position: absolute;
    top: 140px;
    left: 0; right: 0;
    text-align: center;
    font-size: 18px;
    line-height: 1.25;
  }
  .pitch p + p { margin-top: 20px; }

  /* Front */
  .front-art { position: absolute; inset: 0; }
  .portrait {
    position: absolute;
    right: 0; top: 0;
    width: 270px; height: 250px;
    background: radial-gradient(ellipse 60% 62% at 58% 42%, var(--photo-light) 0%, var(--photo-mid) 45%, var(--card-black) 100%);
  }
  .contact {
    position: absolute;
    left: 48px;
    top: 92px;
  }
  .contact__name { color: var(--teal-light); font-size: 22px; font-weight: 600; line-height: 1.2; }
  .contact__title { font-size: 17px; margin-top: 2px; line-height: 1.2; }
  .contact__company { color: var(--teal-light); font-size: 21px; font-weight: 600; margin-top: 22px; line-height: 1.2; }
  .contact__list { list-style: none; margin-top: 8px; font-size: 17px; line-height: 1.35; }
  .contact__list li { display: flex; align-items: center; gap: 10px; }
  .contact__icon { width: 12px; height: 12px; fill: var(--teal-light); flex: none; }
</style>
</head>
<body>

<section class="card card--back" aria-label="Card back">
  <div class="brand">
    <span class="brand__mark"></span>
    <span class="brand__name">Ventrino Real Estate Services</span>
  </div>
  <div class="pitch">
    <p>Don't buy or lease property without someone<br>looking out for your best interests.<br>I will represent you on your home or<br>investment purchase for FREE!</p>
    <p>Home owners, call today to receive a<br>FREE market analysis for your homes value!</p>
  </div>
</section>

<section class="card card--front" aria-label="Card front">
  <div class="portrait" role="img" aria-label="Portrait photo of the broker"></div>
  <svg class="front-art" width="620" height="355" viewBox="0 0 620 355" aria-hidden="true">
    <defs>
      <linearGradient id="silver" x1="0" y1="0" x2="1" y2="0">
        <stop offset="0" stop-color="var(--silver-light)"/>
        <stop offset="0.6" stop-color="var(--silver-dark)"/>
        <stop offset="1" stop-color="var(--silver-light)"/>
      </linearGradient>
    </defs>
    <path d="M0 308 C 200 300, 360 292, 470 237 S 590 176, 620 168 L 620 180 C 580 192, 520 222, 470 252 S 200 312, 0 318 Z" fill="url(#silver)"/>
    <path d="M0 324 C 210 316, 370 306, 476 256 S 590 192, 620 185 L 620 355 L 0 355 Z" fill="var(--teal)"/>
  </svg>
  <div class="contact">
    <div class="contact__name">Carla Ventrino</div>
    <div class="contact__title">Owner &amp; Qualifying Broker</div>
    <div class="contact__company">Ventrino Real Estate Services</div>
    <ul class="contact__list">
      <li><svg class="contact__icon" viewBox="0 0 12 12"><path d="M1 4 Q6 0 11 4 L9 6 L8 4 L4 4 L3 6 Z M2 7 H10 V11 H2 Z"/></svg>505.718.2094</li>
      <li><svg class="contact__icon" viewBox="0 0 12 12"><path d="M0 2 H12 V10 H0 Z M0 2 L6 7 L12 2" stroke="var(--card-black)" stroke-width="1"/></svg>carla@ventrinohomes.example</li>
      <li><svg class="contact__icon" viewBox="0 0 12 12"><circle cx="6" cy="6" r="6"/></svg>www.ventrinohomes.example</li>
    </ul>
  </div>
</section>

</body>
</html>
```